Stationery Design for Fuzzy Pawl Threads - FPT

we are a new company in melbourne
fuzzypawlthreads is a clothing company for your dogs
we need a logo and stationery , scoial media designs done ASAP
list of items needed are
* company Logo
*stationery
bussnes cards
letter head
email signiture
enverlops
lables
etc
* Social Media
Facebook banner and profile pics
tiles for advertising
Instrgram banner and profile pics
tiles foir advertising

open to look at differnets colors themes and fonts

Target Market(s)

anyone with a puppy/ dog

Industry/Entity Type

Pet Clothing

Font styles to use
Serif
Sans Serif
Decorative

Colors

Designer to choose colors to be used in the design.

Requirements
Must have
• must be eye catching and fun
Nice to have
• # so Fetch
Should not have
• pics of any other animals or people on dogs and pups

```html
<!DOCTYPE html>
<html lang="en">
<head>
<meta charset="utf-8">
<title>Fuzzy Pawl Threads – Business Card</title>
<link rel="stylesheet" href="https://fonts.googleapis.com/css2?family=Mali:wght@500;700&display=swap">
<style>
  :root {
    --page-bg: #eeeae6;
    --card-bg: #ffffff;
    --pattern-tint: #f5e6f9;
    --plum: #821e8c;
    --violet: #b624c9;
    --lilac: #e8c3f0;
    --white: #ffffff;
  }
  * { box-sizing: border-box; margin: 0; padding: 0; }
  html, body { width: 1200px; height: 1200px; overflow: hidden; }
  body {
    background: var(--page-bg);
    font-family: "Mali", "Comic Sans MS", cursive;
    position: relative;
  }
  .card {
    position: absolute;
    left: 250px;
    width: 700px;
    height: 400px;
    border-radius: 28px;
    overflow: hidden;
    background: linear-gradient(160deg, var(--card-bg) 0%, var(--pattern-tint) 100%);
    box-shadow: 0 10px 30px rgba(60, 20, 70, 0.18);
  }
  .card--front { top: 170px; }
  .card--back { top: 630px; }

  .card__pattern { position: absolute; inset: 0; }
  .card__band { position: absolute; inset: 0; width: 100%; height: 100%; }
  .card__band path { fill: var(--plum); }

  .mascot {
    position: absolute;
    width: 250px;
    height: 265px;
    border-radius: 48% 48% 44% 44%;
    background: radial-gradient(circle at 50% 35%, var(--lilac) 0%, #d58de2 55%, var(--violet) 100%);
  }
  .card--front .mascot { left: 410px; top: 105px; }
  .card--back .mascot { left: 60px; top: 50px; }

  .wordmark {
    position: absolute;
    left: 56px;
    top: 62px;
    width: 330px;
    color: var(--plum);
    font-weight: 700;
    font-size: 62px;
    line-height: 0.98;
  }
  .wordmark__line { display: block; }

  .social {
    position: absolute;
    left: 52px;
    top: 338px;
    display: flex;
    align-items: center;
    gap: 10px;
    color: var(--white);
    font-weight: 500;
    font-size: 18px;
  }
  .social__dot {
    width: 22px; height: 22px;
    border-radius: 50%;
    background: var(--white);
  }

  .hashtag {
    position: absolute;
    left: 40px;
    top: 322px;
    color: var(--white);
    font-weight: 700;
    font-size: 36px;
  }

  .contact {
    position: absolute;
    left: 370px;
    top: 130px;
    color: var(--plum);
  }
  .contact__name { font-weight: 700; font-size: 40px; line-height: 1.05; }
  .contact__role { font-weight: 500; font-size: 26px; letter-spacing: 1px; margin-top: 2px; }
  .contact__phone { font-weight: 700; font-size: 28px; margin-top: 56px; }
  .contact__line { font-weight: 500; font-size: 18px; line-height: 1.25; }
</style>
</head>
<body>

  <section class="card card--front">
    <div class="card__pattern" role="img" aria-label="Soft lilac pattern of paw prints and dog bones"></div>
    <svg class="card__band" viewBox="0 0 700 400" preserveAspectRatio="none" aria-hidden="true">
      <path d="M0 300 C 110 288 210 298 310 322 S 540 366 700 350 L700 400 L0 400 Z"/>
    </svg>
    <div class="mascot" role="img" aria-label="Cartoon puppy mascot peeking over the band, paws resting on it"></div>
    <h1 class="wordmark">
      <span class="wordmark__line">Fuzzy</span>
      <span class="wordmark__line">Pawl</span>
      <span class="wordmark__line">Threads</span>
    </h1>
    <div class="social">
      <span class="social__dot"></span>
      <span class="social__handle">@fuzzypawlthreads</span>
    </div>
  </section>

  <section class="card card--back">
    <div class="card__pattern" role="img" aria-label="Soft lilac pattern of paw prints and dog bones"></div>
    <svg class="card__band" viewBox="0 0 700 400" preserveAspectRatio="none" aria-hidden="true">
      <path d="M0 225 C 60 232 100 252 150 268 L 290 320 C 315 345 325 372 330 400 L0 400 Z"/>
    </svg>
    <div class="mascot" role="img" aria-label="Cartoon puppy mascot peeking over the band, paws resting on it"></div>
    <p class="hashtag">#WagInStyle</p>
    <div class="contact">
      <p class="contact__name">Lena Corvath</p>
      <p class="contact__role">OWNER</p>
      <p class="contact__phone">(939) 555- 0182</p>
      <p class="contact__line">fuzzypawlthreads@pawmail.com</p>
      <p class="contact__line">fuzzypawlthreads.com</p>
    </div>
  </section>

</body>
</html>
```